Just Sold Postcard

Real Estate/ Brindle Oak Realty.I'd like a template that I can use to change out the picture of the home, verbiage on the front, and address. I'm including a picture of what I've used in the past. I like designs that use red, with some blue and white. I'd like the ability to change the verbiage on the back as well.

Industry/Entity Type

Real Estate

Font styles to use
Serif
Sans Serif

```html
<!DOCTYPE html>
<html lang="en">
<head>
<meta charset="utf-8">
<title>Just Sold Postcard – Brindle Oak Realty</title>
<link href="https://fonts.googleapis.com/css2?family=Lato:wght@400;700;900&family=Open+Sans:wght@600;700&display=swap" rel="stylesheet">
<style>
  :root {
    --stage: #333333;
    --paper: #ffffff;
    --brand-red: #ec2c26;
    --brand-navy: #2e2f7f;
    --text-light: #ffffff;
    --photo-fill: #a87a5e;
  }
  * { box-sizing: border-box; margin: 0; padding: 0; }
  html, body { width: 1200px; height: 1000px; overflow: hidden; }
  body { background: var(--stage); position: relative; font-family: "Lato", sans-serif; }

  .postcard { position: absolute; width: 577px; height: 436px; background: var(--paper); overflow: hidden; }
  .postcard--back { left: 197px; top: 111px; }
  .postcard--front { left: 454px; top: 449px; }

  .brand-name {
    position: absolute; display: flex; align-items: center; gap: 8px;
    font-family: "Lato", sans-serif; font-weight: 900; color: var(--brand-navy);
    white-space: nowrap;
  }
  .brand-name__dot { border-radius: 50%; background: var(--brand-navy); flex: none; }
  .postcard--back .brand-name { left: 41px; top: 52px; font-size: 27px; }
  .postcard--back .brand-name__dot { width: 16px; height: 16px; }
  .postcard--front .brand-name { left: 32px; top: 62px; font-size: 31px; }
  .postcard--front .brand-name__dot { width: 18px; height: 18px; }

  .agent-panel {
    position: absolute; left: 0; top: 111px; width: 280px; height: 246px;
    background: var(--brand-red); color: var(--text-light); padding: 24px 24px 0 41px;
    font-size: 12.5px; line-height: 15px; letter-spacing: 0.4px;
    hyphens: auto; -webkit-hyphens: auto;
  }
  .agent-panel__name { font-size: 27px; font-weight: 700; line-height: 32px; margin-bottom: 10px; letter-spacing: 0.8px; }
  .agent-panel__cta { font-weight: 900; }
  .agent-panel p { margin-bottom: 10px; }
  .agent-panel__blurb { text-align: justify; }

  .front-band {
    position: absolute; left: 0; top: 241px; width: 577px; height: 195px; background: var(--brand-red);
  }
  .headline {
    position: absolute; left: 30px; top: 166px; font-family: "Open Sans", sans-serif; font-weight: 700;
    font-size: 30px; letter-spacing: 2.5px; color: var(--brand-red);
  }
  .front-copy {
    position: absolute; left: 31px; top: 258px; color: var(--text-light);
    font-size: 12.5px; line-height: 17px; letter-spacing: 0.3px;
    hyphens: auto; -webkit-hyphens: auto;
  }
  .front-copy__lead { width: 205px; margin-bottom: 5px; }
  .front-copy__body { width: 262px; }

  .photo-ring { position: absolute; }
  .photo-ring--main { left: 229px; top: 102px; width: 230px; height: 230px; }
  .photo-ring--small { left: 423px; top: 22px; width: 129px; height: 129px; }

  .agent-sign {
    position: absolute; left: 343px; top: 352px; color: var(--text-light);
  }
  .agent-sign__name { font-size: 30px; font-weight: 700; line-height: 34px; letter-spacing: 0.5px; }
  .agent-sign__contact { font-size: 17px; line-height: 22px; letter-spacing: 0.3px; }
  .agent-sign__label { font-weight: 900; margin-right: 8px; letter-spacing: 0.5px; }
</style>
</head>
<body>

<section class="postcard postcard--back">
  <div class="brand-name"><span class="brand-name__dot"></span>Brindle Oak Realty</div>
  <div class="agent-panel">
    <h2 class="agent-panel__name">Dana Whitfield</h2>
    <p>For a free Market Analysis of your home. <span class="agent-panel__cta">Contact me today</span></p>
    <p>Call: (555)-204-3861<br>Email: whitfield.dana@mailbox.com</p>
    <p class="agent-panel__blurb">Lorem ipsum dolor sit amet, consectetur adipiscing elit Duis sed eleifend ex. Donecsapien ante, fermentumnon velit at, convallis suscipit tortor.</p>
  </div>
</section>

<section class="postcard postcard--front">
  <div class="front-band"></div>
  <div class="brand-name"><span class="brand-name__dot"></span>Brindle Oak Realty</div>
  <h1 class="headline">JUST SOLD!</h1>

  <div class="front-copy">
    <p class="front-copy__lead">Lorem ipsum dolor sit amet, consectetur adipiscing elit Duis sed eleife</p>
    <p class="front-copy__body">Lorem ipsum dolor sit amet, consectetur adipiscing elit Duis sed eleifend ex. Donecsapien ante, fermentumnon velit at, convallis suscipit tortor. Proin elementum orci magna. Nulla vestibulum vitae ante</p>
  </div>

  <svg class="photo-ring photo-ring--small" viewBox="0 0 129 129">
    <circle cx="64.5" cy="64.5" r="64.5" fill="var(--brand-navy)"/>
    <circle cx="64.5" cy="64.5" r="57" fill="var(--photo-fill)" role="img" aria-label="Photo of the sold home, second view"/>
  </svg>

  <svg class="photo-ring photo-ring--main" viewBox="0 0 230 230">
    <circle cx="115" cy="115" r="115" fill="var(--brand-navy)"/>
    <circle cx="115" cy="115" r="100" fill="var(--photo-fill)" role="img" aria-label="Photo of the sold home, front view"/>
  </svg>

  <div class="agent-sign">
    <div class="agent-sign__name">Dana Whitfield</div>
    <div class="agent-sign__contact"><span class="agent-sign__label">Contact</span>555-204-3861</div>
  </div>
</section>

</body>
</html>
```